Design a product reviews website

We need a website design and simple logo for the brand Venlotix.com. The website will provide reviews of technology products and services. The brand and website should be approachable but should also be trustworthy and high quality. The deliverable should be designs, specs and assets that I can provide to a development team to build the website.

Target Market(s)

People researching products to buy.

Industry/Entity Type

Product

Logo Text

Venlotix.com

Number of Pages Required

5+ page

Font styles to use
Sans Serif

Colors
0492cd
0355a3
3176b5
33a6d7
85cae6
85abd2
cedeed
cee9f5

Requirements
Must have
• - Designs for the Homepage, Category and Article pages.
• - Designs for web and mobile.
• - Designs details for the engineering team to use for development.
• - I'm open to other colors than the preferences I chose but I'm more likely to like blues, greys and blacks.

```html
<!DOCTYPE html>
<html lang="en">
<head>
<meta charset="utf-8">
<title>Venlotix.com — Product and Service Reviews</title>
<link rel="stylesheet" href="https://fonts.googleapis.com/css2?family=Montserrat:wght@300;400;500&family=Lato:wght@400;700&display=swap">
<style>
  :root {
    --brand: #3a87d9;
    --brand-dark: #0355a3;
    --search-btn: #0492cd;
    --text-dark: #222;
    --text-body: #555;
    --rule: #e3e3e3;
    --load-more: #9a9a9a;
    --footer-bg: #222;
    --white: #fff;
  }
  * { box-sizing: border-box; margin: 0; padding: 0; }
  html, body { width: 871px; height: 1200px; overflow: hidden; background: var(--white); }
  body { font-family: "Lato", sans-serif; color: var(--text-body); position: relative; }

  .site-header {
    height: 61px; border-bottom: 2px solid var(--brand);
    position: relative;
  }
  .brand {
    position: absolute; left: 74px; top: 17px;
    font-family: "Montserrat", sans-serif; font-weight: 500;
    font-size: 20px; color: var(--text-dark); letter-spacing: 0.3px;
    display: flex; align-items: center; gap: 6px;
  }
  .brand-mark { width: 14px; height: 14px; background: var(--search-btn); border-radius: 3px; }
  .search {
    position: absolute; left: 450px; top: 14px; display: flex;
  }
  .search-input {
    width: 282px; height: 28px; border: 1px solid #ccc;
    font-family: "Lato", sans-serif; font-size: 10px; color: #888;
    padding: 0 10px; display: flex; align-items: center;
  }
  .search-btn {
    width: 43px; height: 28px; margin-left: 4px; background: var(--search-btn);
    display: flex; align-items: center; justify-content: center;
  }
  .menu-icon { position: absolute; left: 798px; top: 21px; }

  .hero {
    height: 257px;
    background: radial-gradient(ellipse at 45% 40%, #5a4a44 0%, #3a2c28 45%, #2a1d1a 100%);
    display: flex; align-items: center; justify-content: center;
  }
  .hero-title {
    font-family: "Montserrat", sans-serif; font-weight: 300;
    color: var(--white); font-size: 28px; line-height: 30px;
    text-align: center; letter-spacing: 0.2px;
  }

  .section-title {
    margin-top: 36px; text-align: center;
    font-family: "Montserrat", sans-serif; font-weight: 500;
    font-size: 19px; color: var(--text-dark); letter-spacing: 0.2px;
  }
  .section-title span { color: var(--brand); }
  .section-rule { width: 48px; height: 2px; background: var(--brand); margin: 8px auto 0; }

  .articles { position: absolute; left: 66px; top: 401px; width: 742px; }
  .article { display: flex; height: 238px; position: relative; }
  .article + .article { margin-top: 0; }
  .article:not(:last-child)::after {
    content: ""; position: absolute; left: 0; right: 0; top: 213px;
    height: 1px; background: var(--rule);
  }
  .article-media {
    width: 278px; height: 187px; position: relative; flex: none;
    border: 2px solid #777;
  }
  .media-1 { background: linear-gradient(135deg, #5b3a2c, #2a2420 55%, #6a4a34); }
  .media-2 { background: linear-gradient(135deg, #cfc8c0, #4aa8a8 55%, #e4e0da); }
  .media-3 { background: linear-gradient(135deg, #8a8580, #3a3432 55%, #a07452); }
  .date-badge {
    position: absolute; left: 7px; top: 7px; width: 45px; height: 34px;
    background: var(--brand); color: var(--white); text-align: center;
    font-family: "Montserrat", sans-serif;
  }
  .date-day { font-size: 12px; font-weight: 500; line-height: 14px; margin-top: 4px; }
  .date-month { font-size: 8.5px; line-height: 11px; }
  .article-body { margin-left: 15px; width: 449px; }
  .article-title {
    font-family: "Montserrat", sans-serif; font-weight: 500;
    font-size: 14.6px; color: var(--brand); margin-top: 4px; white-space: nowrap;
  }
  .article-excerpt {
    font-size: 10.3px; line-height: 18.6px; margin: 5px 0 0 2px; width: 446px;
  }
  .read-more {
    margin: 17px 0 0 5px; width: 86px; height: 29px; background: var(--brand);
    color: var(--white); font-size: 9.5px; font-weight: 700;
    display: flex; align-items: center; justify-content: center; gap: 5px;
  }

  .load-more {
    position: absolute; left: 66px; top: 1098px; width: 740px; height: 34px;
    background: var(--load-more); color: var(--white);
    font-family: "Montserrat", sans-serif; font-size: 11px; font-weight: 500;
    display: flex; align-items: center; justify-content: center; gap: 8px;
  }

  .site-footer {
    position: absolute; left: 0; top: 1165px; width: 871px; height: 35px;
    background: var(--footer-bg); color: #ddd; font-size: 10px;
    display: flex; align-items: center; justify-content: center;
  }
</style>
</head>
<body>
  <header class="site-header">
    <div class="brand"><span class="brand-mark"></span>Venlotix.com</div>
    <div class="search">
      <div class="search-input">Search</div>
      <div class="search-btn">
        <svg width="13" height="13" viewBox="0 0 13 13"><circle cx="5.5" cy="5.5" r="4" fill="none" stroke="#fff" stroke-width="2"/><line x1="8.5" y1="8.5" x2="12" y2="12" stroke="#fff" stroke-width="2.2" stroke-linecap="round"/></svg>
      </div>
    </div>
    <svg class="menu-icon" width="17" height="14" viewBox="0 0 17 14" aria-label="Menu">
      <rect x="0" y="0" width="3.5" height="3.5" fill="#222"/><rect x="5" y="0" width="12" height="3.5" fill="#222"/>
      <rect x="0" y="5.2" width="3.5" height="3.5" fill="#222"/><rect x="5" y="5.2" width="12" height="3.5" fill="#222"/>
      <rect x="0" y="10.4" width="3.5" height="3.5" fill="#222"/><rect x="5" y="10.4" width="12" height="3.5" fill="#222"/>
    </svg>
  </header>

  <section class="hero" role="img" aria-label="Smartwatch and fitness band on a wooden table">
    <h1 class="hero-title">The Best Product And Services Reviews<br>And Rankings</h1>
  </section>

  <h2 class="section-title">LATEST <span>ARTICLES</span></h2>
  <div class="section-rule"></div>

  <main class="articles">
    <article class="article">
      <div class="article-media media-1" role="img" aria-label="Wireless music system on a wooden desk">
        <div class="date-badge"><div class="date-day">12</div><div class="date-month">Nov</div></div>
      </div>
      <div class="article-body">
        <h3 class="article-title">We Strongly Feel and Believe “CUTTING....... LEAVE IT TO US”</h3>
        <p class="article-excerpt">Lorem ipsum dolor sit amet, consectetuer adipiscing elit, sed diam nonummy nibh euismod tincidunt ut laoreet dolore magna aliquam erat volutpat. Ut wisi enim ad minim veniam, quis nostrud exerci tation ullamcorper suscipit lobortis nisl ut aliquip ex ea commodo consequat. Duis autem vel eum iriure dolor in hendrerit in vulputate velit esse molestie consequat, vel illum dolore eu feugiat nulla facilisis at vero eros et accumsan et iusto odio dignissim qui blandit praesent luptatum zzril delenit augue duis dolore te feugait nulla facilisi.</p>
        <div class="read-more"><svg width="13" height="9" viewBox="0 0 13 9"><path d="M0.5 4.5 Q6.5 -2 12.5 4.5 Q6.5 11 0.5 4.5Z" fill="none" stroke="#fff" stroke-width="1.2"/><circle cx="6.5" cy="4.5" r="2" fill="#fff"/></svg>Read more</div>
      </div>
    </article>
    <article class="article">
      <div class="article-media media-2" role="img" aria-label="Teal portable speaker on a white table">
        <div class="date-badge"><div class="date-day">12</div><div class="date-month">Nov</div></div>
      </div>
      <div class="article-body">
        <h3 class="article-title">We Strongly Feel and Believe “CUTTING....... LEAVE IT TO US”</h3>
        <p class="article-excerpt">Lorem ipsum dolor sit amet, consectetuer adipiscing elit, sed diam nonummy nibh euismod tincidunt ut laoreet dolore magna aliquam erat volutpat. Ut wisi enim ad minim veniam, quis nostrud exerci tation ullamcorper suscipit lobortis nisl ut aliquip ex ea commodo consequat. Duis autem vel eum iriure dolor in hendrerit in vulputate velit esse molestie consequat, vel illum dolore eu feugiat nulla facilisis at vero eros et accumsan et iusto odio dignissim qui blandit praesent luptatum zzril delenit augue duis dolore te feugait nulla facilisi.</p>
        <div class="read-more"><svg width="13" height="9" viewBox="0 0 13 9"><path d="M0.5 4.5 Q6.5 -2 12.5 4.5 Q6.5 11 0.5 4.5Z" fill="none" stroke="#fff" stroke-width="1.2"/><circle cx="6.5" cy="4.5" r="2" fill="#fff"/></svg>Read more</div>
      </div>
    </article>
    <article class="article">
      <div class="article-media media-3" role="img" aria-label="Video camera with microphone beside a keyboard">
        <div class="date-badge"><div class="date-day">12</div><div class="date-month">Nov</div></div>
      </div>
      <div class="article-body">
        <h3 class="article-title">We Strongly Feel and Believe “CUTTING....... LEAVE IT TO US”</h3>
        <p class="article-excerpt">Lorem ipsum dolor sit amet, consectetuer adipiscing elit, sed diam nonummy nibh euismod tincidunt ut laoreet dolore magna aliquam erat volutpat. Ut wisi enim ad minim veniam, quis nostrud exerci tation ullamcorper suscipit lobortis nisl ut aliquip ex ea commodo consequat. Duis autem vel eum iriure dolor in hendrerit in vulputate velit esse molestie consequat, vel illum dolore eu feugiat nulla facilisis at vero eros et accumsan et iusto odio dignissim qui blandit praesent luptatum zzril delenit augue duis dolore te feugait nulla facilisi.</p>
        <div class="read-more"><svg width="13" height="9" viewBox="0 0 13 9"><path d="M0.5 4.5 Q6.5 -2 12.5 4.5 Q6.5 11 0.5 4.5Z" fill="none" stroke="#fff" stroke-width="1.2"/><circle cx="6.5" cy="4.5" r="2" fill="#fff"/></svg>Read more</div>
      </div>
    </article>
  </main>

  <div class="load-more">
    <svg width="18" height="18" viewBox="0 0 18 18"><path d="M3 9 A6 6 0 0 1 14 5.5" fill="none" stroke="#fff" stroke-width="1.6"/><path d="M15 9 A6 6 0 0 1 4 12.5" fill="none" stroke="#fff" stroke-width="1.6"/><path d="M14.5 2 L14.5 6 L10.5 6" fill="none" stroke="#fff" stroke-width="1.6"/><path d="M3.5 16 L3.5 12 L7.5 12" fill="none" stroke="#fff" stroke-width="1.6"/></svg>
    Load More
  </div>

  <footer class="site-footer">Copyright © 2016&nbsp; Venlotix.com. All Rights Reserved.</footer>
</body>
</html>
```